Modern card design needed for building development company

We are looking for a sharp modern new look for our business cards.
We are a New Zealand based company called TKR Ventures NZ LTD that specialises in subdividing large sections, housing and commercial buildings.
We have attached a photo of the current logo and would like to see it improved somehow as it looks a bit dated.
We are open to any colours.

Target Market(s)

Investors, Property buyers

Industry/Entity Type

Investment

Contact Information for Business Card

TKR VENTURES NZ LTD
www.tkrventuresnz.co.nz

Damon Whitcombe
Phone +64 21 938 104
Email dpwhitcombe@korumail.co.nz

Font styles to use
Serif
Sans Serif

Colors
0792cd
33a6d7
85cae6
6b449b
886aae
f04a50
ec1f27
f37122
f68d4d

Requirements
Must have
• Please try and make the logo more modern or if you have a similar one we would like to see it.

```html
<!DOCTYPE html>
<html lang="en">
<head>
<meta charset="utf-8">
<title>TKR Ventures NZ LTD – Business Card</title>
<link rel="stylesheet" href="https://fonts.googleapis.com/css2?family=Open+Sans:wght@400;600&display=swap">
<style>
  :root {
    --page-bg: #e4e2e0;
    --card-orange: #e8731b;
    --card-frost: #ecebea;
    --badge-frost: #f6f5f4;
    --text-light: #ffffff;
    --text-dark: #3a3a3a;
  }
  html, body {
    margin: 0;
    width: 1200px;
    height: 900px;
    overflow: hidden;
    background: var(--page-bg);
    font-family: "Open Sans", Arial, sans-serif;
  }
  .business-card {
    position: absolute;
    left: 180px;
    top: 196px;
    width: 840px;
    height: 509px;
    filter: drop-shadow(0 6px 14px rgba(0,0,0,0.12));
  }
  .card-name { font-size: 24px; font-weight: 400; fill: var(--text-light); }
  .card-role { font-size: 15.5px; font-weight: 400; fill: var(--text-light); }
  .card-contact { font-size: 16px; font-weight: 400; fill: var(--text-light); }
  .company-name { font-size: 30px; font-weight: 600; fill: var(--text-dark); letter-spacing: 1px; }
  .company-suffix { font-size: 30px; font-weight: 600; fill: var(--text-dark); letter-spacing: 1px; }
</style>
</head>
<body>
<svg class="business-card" viewBox="0 0 685 415" xmlns="http://www.w3.org/2000/svg" role="img" aria-label="TKR Ventures NZ LTD business card for Damon Whitcombe">
  <defs>
    <clipPath id="card-outline">
      <rect x="0" y="0" width="476" height="415"/>
      <circle cx="476" cy="207.5" r="207.5"/>
    </clipPath>
  </defs>

  <g clip-path="url(#card-outline)">
    <!-- card body -->
    <rect class="card-body" x="0" y="0" width="685" height="415" fill="var(--card-frost)"/>
    <!-- orange bands -->
    <rect class="band-top" x="0" y="0" width="685" height="115" fill="var(--card-orange)"/>
    <rect class="band-bottom" x="0" y="295" width="685" height="120" fill="var(--card-orange)"/>
    <!-- right badge ring -->
    <circle class="badge-ring" cx="476" cy="207.5" r="207.5" fill="var(--card-orange)"/>
    <circle class="badge" cx="476" cy="207.5" r="200" fill="var(--badge-frost)"/>
  </g>

  <!-- name block -->
  <text class="card-name" x="30" y="60">Damon Whitcombe</text>
  <text class="card-role" x="30" y="85">Managing Director</text>

  <!-- company name -->
  <rect class="company-mark" x="468" y="150" width="18" height="18" fill="var(--card-orange)"/>
  <text class="company-name" x="477" y="215" text-anchor="middle">TKR VENTURES</text>
  <text class="company-suffix" x="477" y="252" text-anchor="middle">NZ LTD</text>

  <!-- contacts -->
  <g class="icon-phone" fill="var(--text-light)" transform="translate(31,321)">
    <path d="M2.5 0.5 L5 0.5 L6.2 3.4 L4.6 4.6 C5.4 6.4 6.7 7.7 8.5 8.5 L9.7 6.9 L12.5 8.1 L12.5 10.6 C12.5 11.4 11.9 12 11.1 12 C5.4 11.6 1.2 7.4 0.8 1.8 C0.8 1.1 1.6 0.5 2.5 0.5 Z"/>
  </g>
  <text class="card-contact" x="56" y="333">+64 21 938 104</text>

  <g class="icon-mail" transform="translate(31,347)">
    <rect x="0" y="0" width="13" height="10" fill="var(--text-light)"/>
    <path d="M0.5 0.8 L6.5 5.5 L12.5 0.8" fill="none" stroke="var(--card-orange)" stroke-width="1.3"/>
  </g>
  <text class="card-contact" x="56" y="357">dpwhitcombe@korumail.co.nz</text>

  <g class="icon-link" fill="none" stroke="var(--text-light)" stroke-width="1.8" transform="translate(31,370) rotate(-45 7 7)">
    <rect x="0" y="4" width="8" height="6" rx="3"/>
    <rect x="6" y="4" width="8" height="6" rx="3"/>
  </g>
  <text class="card-contact" x="56" y="381">www.tkrventuresnz.co.nz</text>
</svg>
</body>
</html>
```